Business Card for Coastal Tundrabridge Advisory

We need a business card for Coastal Tundrabridge Advisory. The company website address is provided below. The company logo is attached. We provide specialized permafrost services to the mining, transportation, and oil & gas industries. The card should be prepared for:
Matthias Korhonen, PhD.
Coastal Tundrabridge Advisory
PO Box 418259
Quillwater, Alaska 99642
Direct: +1-907-555-0143
Email: mkorhonen@tundrabridgeadvisory.example
Website: www.coastaltundrabridgeadvisory.example

```html
<!DOCTYPE html>
<html lang="en">
<head>
<meta charset="utf-8">
<title>Coastal Tundrabridge Advisory – Business Card</title>
<link rel="stylesheet" href="https://fonts.googleapis.com/css2?family=Roboto:wght@300;400;500;700&display=swap">
<style>
  :root {
    --backdrop: #2b2b2c;
    --card: #0f1521;
    --card-edge: #161d2b;
    --ink: #ffffff;
    --ink-soft: #d9dde6;
    --emboss: #1b2331;
    --brand-blue: #2c3f8e;
  }
  * { margin: 0; padding: 0; box-sizing: border-box; }
  html, body { width: 1200px; height: 780px; overflow: hidden; }
  body {
    background: var(--backdrop);
    font-family: "Roboto", Arial, sans-serif;
    color: var(--ink);
    display: flex;
    align-items: center;
    justify-content: center;
    gap: 44px;
  }
  .card {
    position: relative;
    width: 540px;
    height: 309px;
    background: var(--card);
    box-shadow: 0 18px 40px rgba(0,0,0,.55);
    overflow: hidden;
  }

  /* Front */
  .card__tab {
    position: absolute;
    top: 0; right: 14px;
    width: 14px; height: 46px;
    background: var(--ink);
  }
  .holder {
    position: absolute;
    top: 18px; right: 40px;
    text-align: right;
    line-height: 1;
  }
  .holder__name { font-size: 27px; }
  .holder__first { font-weight: 700; }
  .holder__last { font-weight: 300; }
  .holder__degree {
    display: block;
    margin-top: 4px;
    font-size: 13px;
    font-weight: 700;
  }
  .wordmark {
    font-family: "Roboto", Arial, sans-serif;
    font-weight: 500;
    letter-spacing: .04em;
    line-height: 1.1;
  }
  .wordmark--front {
    position: absolute;
    left: 36px; top: 96px;
    font-size: 22px;
    color: var(--ink);
    width: 230px;
  }
  .wordmark--emboss {
    position: absolute;
    right: 26px; bottom: 108px;
    font-size: 19px;
    color: var(--emboss);
    width: 210px;
    text-align: right;
  }
  .address {
    position: absolute;
    left: 36px; top: 186px;
    font-size: 12.5px;
    font-weight: 400;
    line-height: 1.35;
    color: var(--ink-soft);
  }
  .contact {
    position: absolute;
    left: 36px; top: 228px;
    list-style: none;
    font-size: 12px;
    line-height: 1;
    color: var(--ink-soft);
  }
  .contact__item {
    display: flex;
    align-items: center;
    gap: 8px;
    margin-bottom: 6px;
  }
  .contact__icon { width: 14px; height: 14px; flex: none; }

  /* Back */
  .wordmark--back {
    position: absolute;
    left: 0; right: 0; top: 92px;
    text-align: center;
    font-size: 34px;
    color: var(--brand-blue);
    letter-spacing: .05em;
  }
  .services {
    position: absolute;
    left: 24px; right: 24px; bottom: 34px;
    text-align: center;
    color: var(--ink);
  }
  .services__title {
    font-size: 12px;
    font-weight: 500;
    letter-spacing: .02em;
    margin-bottom: 6px;
  }
  .services__text {
    font-size: 11.5px;
    font-weight: 400;
  }
</style>
</head>
<body>

  <section class="card card--front" aria-label="Business card front">
    <div class="card__tab"></div>
    <div class="holder">
      <div class="holder__name"><span class="holder__first">Matthias</span> <span class="holder__last">Korhonen</span></div>
      <span class="holder__degree">PhD</span>
    </div>

    <div class="wordmark wordmark--front">Coastal Tundrabridge Advisory</div>

    <p class="address">PO Box 418259<br>Quillwater, Alaska 99642</p>

    <ul class="contact">
      <li class="contact__item">
        <svg class="contact__icon" viewBox="0 0 14 14" aria-hidden="true">
          <circle cx="7" cy="7" r="7" fill="#fff"/>
          <path d="M4.6 3.6l1.3 1.3-.7 1c.5 1.1 1.2 1.8 2.3 2.3l1-.7 1.3 1.3-.9 1.1C6.6 9.7 4.3 7.4 3.5 4.5z" fill="#0f1521"/>
        </svg>
        <span>+1-907-555-0143</span>
      </li>
      <li class="contact__item">
        <svg class="contact__icon" viewBox="0 0 14 14" aria-hidden="true">
          <circle cx="7" cy="7" r="7" fill="#fff"/>
          <rect x="3.4" y="4.6" width="7.2" height="5" fill="none" stroke="#0f1521" stroke-width="1"/>
          <path d="M3.4 4.6L7 7.4l3.6-2.8" fill="none" stroke="#0f1521" stroke-width="1"/>
        </svg>
        <span>mkorhonen@tundrabridgeadvisory.example</span>
      </li>
      <li class="contact__item">
        <svg class="contact__icon" viewBox="0 0 14 14" aria-hidden="true">
          <circle cx="7" cy="7" r="7" fill="#fff"/>
          <circle cx="7" cy="7" r="3.8" fill="none" stroke="#0f1521" stroke-width="1"/>
          <ellipse cx="7" cy="7" rx="1.6" ry="3.8" fill="none" stroke="#0f1521" stroke-width=".9"/>
          <path d="M3.2 7h7.6" stroke="#0f1521" stroke-width=".9"/>
        </svg>
        <span>www.coastaltundrabridgeadvisory.example</span>
      </li>
    </ul>

    <div class="wordmark wordmark--emboss" aria-hidden="true">Coastal Tundrabridge Advisory</div>
  </section>

  <section class="card card--back" aria-label="Business card back">
    <div class="wordmark wordmark--back">Coastal Tundrabridge<br>Advisory</div>
    <div class="services">
      <h2 class="services__title">OUR SERVICES</h2>
      <p class="services__text">We provide specialized permafrost services to the mining, transportation, and oil &amp; gas industries</p>
    </div>
  </section>

</body>
</html>
```